Web Design Project

i'm looking for a sleek modern design i can use for a web site that deals with.
Intelligent Data Capture
Accounts Payable Solutions for faster processing based on our scanning solution.
ultimately we are a intelligent scanning software.

here is a great website, that does exactly what we do, and we like to have most of their services and products.

so something in this idea would be great.
www.valtrino.com

so i guess i want a good landing/home page which is smartly designed so users will be inclined to leave their information.

and then information pages.

also i dont need any cms for you to include, i only need you to hook the html hooks for RANK Kettle as i already have a CMS and need it to hook in to that, i am including links to that cheat sheet.
so it is easier when included as you create the Theme.

http://www.rankkettle.com/how-to-create-website-template.html
http://www.rankkettle.com/cheat-sheet.html
Updates

Hi Guys sorry for the long pause in design, but here is where we stand.

what ever design i choose, i need that designer to customize a few things for me based on design that was designed.
and i will need designer to match that them to work with RANK Kettle
here is the cheat sheet for the hooks that we need to match and make it work.
if you have any questions let me know.

otherwise i look forward to working with you. and good luck.

Target Market(s)

CFO's AP Managers, mostly ppl who are not Tech freindly

Industry/Entity Type

Software

Requirements
Must have
• i need on home page, the rotating banner should have 1 ability to place youtube links to show videos, and also ability to add buttons on these rotating banners that will allow forms to pop up take to another page.

```html
<!DOCTYPE html>
<html lang="en">
<head>
<meta charset="utf-8">
<title>KORVA — Intelligent Data Capture</title>
<link href="https://fonts.googleapis.com/css2?family=Bebas+Neue&family=Source+Sans+3:wght@400;600&display=swap" rel="stylesheet">
<style>
:root{
  --header:#2a2a2a;
  --header-line:#555;
  --accent:#4fc3ef;
  --muted:#a9a9a9;
  --text:#222;
  --card-border:#d6d6d6;
  --btn-top:#a9e2f7;
  --btn-bottom:#5cc2ea;
  --btn-text:#1d6d92;
  --red:#c8161d;
  --green-top:#e9f9a1;
  --green-bottom:#c2e04a;
  --footer:#2c2c2c;
  --footer-text:#dcdcdc;
}
*{margin:0;padding:0;box-sizing:border-box}
html,body{width:1200px;height:1184px;overflow:hidden}
body{position:relative;background:linear-gradient(135deg,#f5f5f5,#ececec);font-family:"Source Sans 3",sans-serif;color:var(--text)}
.abs{position:absolute}

.site-header{position:absolute;left:0;top:0;width:1200px;height:120px;background:linear-gradient(160deg,#333 0%,#262626 60%,#2e2e2e 100%)}
.brand{position:absolute;left:216px;top:28px;font-family:"Source Sans 3",sans-serif;font-weight:600;font-size:30px;line-height:36px;color:#fff;white-space:nowrap}
.utility{position:absolute;right:216px;top:18px;font-size:9.5px;color:#ddd;display:flex;gap:8px;align-items:center}
.utility .flag{width:19px;height:12px;background:#2b4a9a;border:1px solid #c33}
.search{position:absolute;left:832px;top:46px;width:126px;height:18px;background:#fff;border-radius:2px;font-size:9.5px;line-height:18px;padding-left:6px;color:#333}
.search-btn{position:absolute;left:966px;top:46px;width:18px;height:18px;border-radius:50%;background:#bbb}
.main-nav{position:absolute;left:216px;top:84px;display:flex}
.main-nav a{display:block;width:94px;margin-right:2px;text-align:center;text-decoration:none;color:#9a9a9a;font-family:"Bebas Neue",sans-serif;font-size:15.5px;padding-top:13px;border-top:2px solid var(--header-line)}
.main-nav a.active{color:var(--accent);border-top-color:var(--accent)}

.hero{position:absolute;left:216px;top:154px;width:768px;height:284px;background:#fff;box-shadow:0 6px 8px -4px rgba(0,0,0,.35)}
.hero-photo{position:absolute;left:5px;top:4px;width:758px;height:276px;background:radial-gradient(ellipse at 30% 55%,#d8a48d 0%,#a9b9cf 30%,#5d8fc4 60%,#3b6fa8 100%)}
.hero-copy{position:absolute;left:0;top:0;width:768px;text-align:center;color:#fff;font-family:"Bebas Neue",sans-serif;text-shadow:0 1px 3px rgba(0,0,0,.5)}
.hero-title{position:absolute;left:0;top:86px;width:768px;font-size:56px;line-height:1}
.hero-line{position:absolute;left:0;width:768px;font-size:29px;line-height:1}
.hero-arrow{position:absolute;top:277px;width:36px;height:36px;border-radius:50%;background:radial-gradient(circle at 40% 35%,#f4f4f4,#bcbcbc)}
.hero-arrow svg{position:absolute;left:8px;top:8px}

.feature{position:absolute;top:480px;width:180px;height:248px;background:#fff;border:1px solid var(--card-border);text-align:center}
.feature-art{position:absolute;left:45px;top:8px;width:90px;height:84px;border-radius:8px}
.feature h3{position:absolute;left:0;top:106px;width:178px;font-family:"Bebas Neue",sans-serif;font-weight:400;font-size:19px;color:var(--muted)}
.feature h3 span{color:var(--accent)}
.feature p{position:absolute;left:8px;top:132px;width:162px;font-size:9px;line-height:14.4px;color:#444}
.learn{position:absolute;left:49px;top:213px;width:80px;height:24px;border-radius:2px;background:linear-gradient(var(--btn-top),var(--btn-bottom));border:1px solid #4aa9d1;font-family:"Bebas Neue",sans-serif;font-size:15px;line-height:23px;color:var(--btn-text)}

.section-title{position:absolute;top:762px;font-family:"Bebas Neue",sans-serif;font-size:29px;color:var(--muted);font-weight:400}
.section-title span{color:var(--accent)}
.welcome p{position:absolute;left:216px;width:490px;font-size:9.3px;line-height:16px;color:#111}
.how-intro{position:absolute;left:744px;top:805px;font-size:9.3px;color:#111}
.how-intro span{color:var(--red)}
.video{position:absolute;left:744px;top:832px;width:240px;height:152px;background:#222;border:2px solid #333}
.video-still{position:absolute;left:0;top:0;width:236px;height:134px;background:linear-gradient(120deg,#d9d9d9,#9aa2ab 55%,#7d8791)}
.play{position:absolute;left:96px;top:52px;width:44px;height:28px;background:rgba(30,30,30,.8);border-radius:3px}
.controls{position:absolute;left:0;top:134px;width:236px;height:14px;background:#1a1a1a;font-size:6px;color:#aaa;line-height:14px}

.cta-band{position:absolute;left:216px;top:1024px;width:768px;height:56px;background:linear-gradient(#eaeaea,#dcdcdc);border:1px solid #cfcfcf}
.cta-brand{position:absolute;left:16px;top:15px;font-family:"Source Sans 3",sans-serif;font-weight:600;font-size:22px;line-height:26px;color:#222}
.cta-divider{position:absolute;left:104px;top:8px;width:1px;height:40px;background:#c6c6c6}
.cta-band p{position:absolute;left:152px;top:6px;width:400px;font-size:9.1px;line-height:14.4px;color:#222}
.cta-btn{position:absolute;top:15px;width:80px;height:24px;border-radius:2px;font-family:"Bebas Neue",sans-serif;font-size:16px;line-height:24px;text-align:center}
.cta-login{left:584px;background:linear-gradient(var(--green-top),var(--green-bottom));color:#5b7a12;border:1px solid #a8c83a}
.cta-contact{left:672px;background:var(--red);color:#fff;border:1px solid #9e0f14}

.site-footer{position:absolute;left:0;top:1120px;width:1200px;height:64px;background:var(--footer);color:var(--footer-text);font-size:9px}
.site-footer .row{position:absolute;white-space:nowrap}
.social{position:absolute;left:888px;top:12px;display:flex;gap:4px}
.social i{display:block;width:16px;height:16px;border-radius:50%;background:#4b8fc9}
</style>
</head>
<body>

<header class="site-header">
  <div class="brand">KORVA</div>
  <div class="utility"><span class="flag"></span><span>▾ &nbsp;|</span><span>Find us</span><span>|</span><span>Login</span></div>
  <div class="search">Search</div>
  <div class="search-btn"></div>
  <nav class="main-nav">
    <a class="active" href="#">Home</a><a href="#">About Us</a><a href="#">Solutions</a><a href="#">Technologies</a><a href="#">Tech Support</a><a href="#">Our Blog</a><a href="#">Partners</a><a href="#">Contact Us</a>
  </nav>
</header>

<section class="hero">
  <div class="hero-photo" role="img" aria-label="Photo of a hand touching a tablet screen in blue light"></div>
  <div class="hero-copy">
    <div class="hero-title">KORVA</div>
    <div class="hero-line" style="top:140px">We have an ultimate scanning software.</div>
    <div class="hero-line" style="top:169px">Intelligent data capture from online sites</div>
  </div>
</section>
<div class="hero-arrow" style="left:231px"><svg width="20" height="20" viewBox="0 0 20 20"><path d="M16 10H5M10 4 4 10l6 6" stroke="#666" stroke-width="3" fill="none"/></svg></div>
<div class="hero-arrow" style="left:933px"><svg width="20" height="20" viewBox="0 0 20 20"><path d="M4 10h11M10 4l6 6-6 6" stroke="#666" stroke-width="3" fill="none"/></svg></div>

<div class="feature" style="left:216px">
  <div class="feature-art" role="img" aria-label="Illustration of a globe on a map" style="background:radial-gradient(circle,#2f8fcf 0%,#1d5f98 45%,#d9c58c 70%,#fff 72%)"></div>
  <h3>About <span>Korva</span></h3>
  <p>Lorem ipsum dolor sit amet, consectetur adipisicing elit, sed do eiusmod tempor incididunt ut labore et dolore magna aliqua. Ut enim ad minim veniam, quis nostrud exercitation .</p>
  <div class="learn">Learn More</div>
</div>
<div class="feature" style="left:412px">
  <div class="feature-art" role="img" aria-label="Illustration of a laptop with a cloud of gears" style="background:radial-gradient(ellipse at 50% 40%,#4a5a6a 0%,#8796a5 45%,#fff 72%)"></div>
  <h3>Intelligent <span>Data Capture</span></h3>
  <p>Lorem ipsum dolor sit amet, consectetur adipisicing elit, sed do eiusmod tempor incididunt ut labore et dolore magna aliqua. Ut enim ad minim veniam, quis nostrud exercitation .</p>
  <div class="learn">Learn More</div>
</div>
<div class="feature" style="left:608px">
  <div class="feature-art" role="img" aria-label="Illustration of a monitor, tablet and stacked papers" style="background:radial-gradient(ellipse,#333 0%,#8a8a8a 45%,#fff 72%)"></div>
  <h3>Technology in <span>Korva</span></h3>
  <p>Lorem ipsum dolor sit amet, consectetur adipisicing elit, sed do eiusmod tempor incididunt ut labore et dolore magna aliqua. Ut enim ad minim veniam, quis nostrud exercitation .</p>
  <div class="learn">Learn More</div>
</div>
<div class="feature" style="left:804px">
  <div class="feature-art" role="img" aria-label="Illustration of figures pushing red gears" style="background:radial-gradient(ellipse at 60% 40%,#e3262b 0%,#e87a7c 40%,#fff 72%)"></div>
  <h3>Tech <span>Support</span></h3>
  <p>Lorem ipsum dolor sit amet, consectetur adipisicing elit, sed do eiusmod tempor incididunt ut labore et dolore magna aliqua. Ut enim ad minim veniam, quis nostrud exercitation .</p>
  <div class="learn">Learn More</div>
</div>

<section class="welcome">
  <h2 class="section-title" style="left:216px">Welcome to <span>Korva</span></h2>
  <p style="top:803px">Ut enim ad minim veniam, quis nostrud exercitation ullamco laboris nisi ut aliquip ex ea commodo consequat. Duis aute irure dolor in reprehenderit in voluptate velit esse cillum dolore eu fugiat nulla pariatur. Excepteur sint occaecat cupidatat non proident, sunt in culpa qui officia deserunt mollit anim id est laborum.</p>
  <p style="top:867px">Lorem ipsum dolor sit amet, consectetur adipisicing elit, sed do eiusmod tempor incididunt ut labore et dolore magna aliqua laborum.Lorem ipsum dolor sit amet, consectetur adipisicing elit.</p>
  <p style="top:915px">Lorem ipsum dolor sit amet, consectetur adipisicing elit, sed do eiusmod tempor incididunt ut labore et dolore magna aliqua. Lorem ipsum dolor sit amet, consectetur adipisicing elit, sed do eiusmod tempor incididunt ut labore et dolore magna aliqua. .Ut enim ad minim veniam, quis nostrud exercitation ullamco laboris nisi ut aliquip ex ea commodo consequat. Duis aute irure dolor in reprehenderit in voluptate velit esse cillum dolore eu fugiat nulla pariatur.</p>
</section>

<section class="how">
  <h2 class="section-title" style="left:744px">How <span>Korva</span> works</h2>
  <div class="how-intro">Ut enim ad minim veniam, quis . <span>Watch Video below!</span></div>
  <div class="video">
    <div class="video-still" role="img" aria-label="Video still of a technician with a laptop beside solar panels"></div>
    <div class="play"><svg width="44" height="28" viewBox="0 0 44 28"><path d="M18 8v12l10-6z" fill="#fff"/></svg></div>
    <div class="controls">
      <svg class="abs" style="left:3px;top:3px" width="8" height="8" viewBox="0 0 8 8"><path d="M1 0v8l6-4z" fill="#ccc"/></svg>
      <span class="abs" style="left:13px;top:5px;width:150px;height:4px;background:#444;border-radius:2px"><span class="abs" style="left:0;top:0;width:95px;height:4px;background:#999;border-radius:2px"></span></span>
      <span class="abs" style="left:172px">1:02 / 2:00 &nbsp;HD</span>
    </div>
  </div>
</section>

<aside class="cta-band">
  <div class="cta-brand">KORVA</div>
  <div class="cta-divider"></div>
  <p>Lorem ipsum dolor sit amet, consectetur adipisicing elit, sed do eiusmod tempor incididunt ut labore et dolore magna aliqua. Ut enim ad minim veniam, quis nostrud exercitation ullamco laboris nisi ut aliquip ex ea commodo consequat.</p>
  <div class="cta-btn cta-login">Login</div>
  <div class="cta-btn cta-contact">Contact</div>
</aside>

<footer class="site-footer">
  <div class="row" style="left:216px;top:15px">Quick links - Register your Product &nbsp;: &nbsp;Tech Support &nbsp;: &nbsp;Sitemap &nbsp;: &nbsp;Korva Worldwide</div>
  <div class="row" style="left:589px;top:15px">Contact us &nbsp;&nbsp;&nbsp; Toll free: 800.555.0147 &nbsp;| &nbsp;Fax: 608.555.0193</div>
  <div class="social"><i></i><i></i><i></i><i></i><i style="background:#e2672a"></i></div>
  <div class="row" style="left:212px;top:41px">© KORVA 2013 | Safe Harbor Privacy Policy | KORVA Fax Server &amp; Fax services</div>
  <div class="row" style="right:216px;top:41px">KORVA Fax &nbsp;| &nbsp;KORVA NetFax &nbsp;| &nbsp;TermLink &nbsp;| &nbsp;Relay Plus &nbsp;| &nbsp;Legal</div>
</footer>

</body>
</html>
```